plumbers buisness card

A buisness card for a plumbing buisness
needs to have a water theme with navy blue, light blue and white
with an image of either a water drop, pipes, tools or something relating to plumbing and incorperating my buisness name as a logo

"Kettering Plumbing" is the words that need to stand out with "& gasfitting" to be smaller

spelling error on brief, "maintenance"
and also could you include my email d_kettering@mailwave.com.au

Industry/Entity Type

Plumbing

Contact Information for Business Card

Kettering Plumbing & Gasfitting

declan kettering
0432961085

specialising in
-new homes
-maitenance
-renovations

license no.
-73840

```html
<!DOCTYPE html>
<html lang="en">
<head>
<meta charset="utf-8">
<title>Kettering Plumbing &amp; Gasfitting – Business Card</title>
<link href="https://fonts.googleapis.com/css2?family=Source+Sans+3:wght@400;600;700&display=swap" rel="stylesheet">
<style>
  :root {
    --board: #f0999b;
    --navy: #233c77;
    --white: #ffffff;
    --label: #2a1f1f;
    --steel-light: #b9c0c8;
    --steel-dark: #5f6b7a;
  }
  * { margin: 0; padding: 0; box-sizing: border-box; }
  html, body {
    width: 1200px; height: 439px; overflow: hidden;
    background: var(--board);
    font-family: "Source Sans 3", "Myriad Pro", Arial, sans-serif;
  }
  .board { position: relative; width: 1200px; height: 439px; }
  .side-label {
    position: absolute;
    font-family: Arial, Helvetica, sans-serif;
    font-size: 28px; color: var(--label); font-weight: 400;
    transform: translateX(-50%);
  }
  .side-label--front { left: 305px; top: 22px; }
  .side-label--back { left: 883px; top: 17px; }

  .card {
    position: absolute; width: 533px; height: 304px;
    background: var(--navy); color: var(--white); overflow: hidden;
  }
  .card--front { left: 54px; top: 90px; }
  .card--back { left: 626px; top: 91px; }

  .tap-photo {
    position: absolute; left: 0; top: 0; width: 210px; height: 280px;
    background: linear-gradient(160deg, var(--steel-light) 0%, var(--steel-dark) 100%);
  }

  .front-text { position: absolute; right: 23px; text-align: right; white-space: nowrap; }
  .owner-name { top: 27px; font-size: 17.5px; font-weight: 700; }
  .owner-phone { top: 51px; font-size: 14.5px; font-weight: 700; letter-spacing: 0.4px; }
  .brand-name { top: 118px; font-size: 34px; font-weight: 700; }
  .brand-sub { top: 155px; font-size: 29px; font-weight: 400; }
  .front-rule { position: absolute; left: 222px; right: 20px; top: 202px; height: 1px; background: var(--white); }
  .services { top: 206px; font-size: 14.5px; font-weight: 700; line-height: 20px; }
  .services-title { font-size: 16px; }
  .services .plain { font-weight: 400; }

  .back-text { position: absolute; left: 0; right: 0; text-align: center; white-space: nowrap; }
  .back-brand { top: 78px; font-size: 34px; font-weight: 700; }
  .back-sub { top: 114px; font-size: 29px; font-weight: 400; }
  .back-rule { position: absolute; left: 86px; width: 360px; top: 174px; height: 1px; background: var(--white); }
  .back-contact { top: 188px; font-size: 33px; font-weight: 700; letter-spacing: 0.3px; }
</style>
</head>
<body>
<main class="board">
  <div class="side-label side-label--front">Front</div>
  <div class="side-label side-label--back">Back</div>

  <section class="card card--front">
    <div class="tap-photo" role="img" aria-label="Photo of a chrome tap with a water droplet falling from the spout"></div>
    <div class="front-text owner-name">Declan Kettering</div>
    <div class="front-text owner-phone">0432961085</div>
    <div class="front-text brand-name">Kettering Plumbing</div>
    <div class="front-text brand-sub">&amp; gasfitting</div>
    <div class="front-rule"></div>
    <div class="front-text services">
      <div class="services-title">Specialising in :</div>
      <div>New homes - Maintenance - Renovations</div>
      <div>email : <span class="plain">d_kettering@mailwave.com.au</span></div>
      <div>license no. 73840</div>
    </div>
  </section>

  <section class="card card--back">
    <div class="back-text back-brand">Kettering Plumbing</div>
    <div class="back-text back-sub">&amp; Gasfitting</div>
    <div class="back-rule"></div>
    <div class="back-text back-contact">CONTACT : 0432961085</div>
  </section>
</main>
</body>
</html>
```